Responsive Mobile Quelvo Jewelry Template

We need to adapt an existing Quelvo template to be 100% responsive and mobile friendly. Due to Quelvo rules, the template would need to be implemented only using HTML and CSS (no Javascript). The template design files and HTML/CSS files are required for this project. We prefer that it is implemented using a responsive framework such as Gridwell.

An example of our current template can be found here (diamond only):
https://www.quelvo-market.example/itm/507318829106?ViewItem=&item=507318829106

And example of our template with an additional section for gemstone:
https://www.quelvo-market.example/itm/507318826673?ViewItem=&item=507318826673

We had also somewhat recently designed our Quelvo store landing page so some consistency with this would be desired:
http://www.quelvoshops.example/MirrowCraftNV

Please also refer to our website: https://mirrowcraftnv.example/

Target Market(s)

Primarily women shopping for jewelry on Quelvo.

Industry/Entity Type

Jewelry

Coding

Coded - Design and coding required

Number of Pages Required

1 page

Font styles to use
Sans Serif

Requirements
Must have
• * A color scheme that fits with the existing template design.
• * REMOVE the product photo in the template.
• * Sections required for Description, Basic Details, and Diamond/Gemstone Details.
• * Please refer to https://pages.quelvo-market.example/sell/itemdescription/mobilefriendlyguidelines.html in particular, the template must use
Nice to have
• * Menu of links to other categories is desired in a mobile friendly way.
• * We are open to graphics for links to popular categories similar to those found on the store page.
• * Implemented using a standardized responsive framework such as Gridwell.

```html
<!DOCTYPE html>
<html lang="en">
<head>
<meta charset="utf-8">
<title>Mirrow Craft Nevada – Item Listing</title>
<link href="https://fonts.googleapis.com/css2?family=Open+Sans:ital,wght@0,400;0,600;0,700;1,700&family=Arimo:wght@400&display=swap" rel="stylesheet">
<style>
:root{
  --purple:#80689e;
  --purple-dark:#6b5289;
  --lilac:#f0e8fb;
  --lilac-mid:#e9def8;
  --ink:#333333;
  --accent-text:#5b1f9a;
  --page:#f2f2f2;
  --white:#ffffff;
  --rule:#d9d9d9;
}
*{box-sizing:border-box;margin:0;padding:0}
html,body{width:1080px;height:1200px;overflow:hidden}
body{background:var(--page);font-family:"Open Sans",sans-serif;color:var(--ink);position:relative}
.sheet{position:absolute;left:18px;top:30px;width:1032px;height:1006px;background:var(--white)}
.page-band{position:absolute;left:0;top:1036px;width:1080px;height:164px;background:var(--white);border-top:1px solid var(--rule)}
.page-band .base{position:absolute;left:0;bottom:0;width:100%;height:20px;background:var(--page)}
.to-top{position:absolute;left:1030px;top:44px;width:22px;height:26px;background:var(--white);border:1px solid #ddd;display:flex;align-items:center;justify-content:center}

.masthead{position:absolute;left:42px;top:34px;width:956px;height:76px;background:linear-gradient(#e2d6f5,var(--white))}
.topnav{height:22px;background:var(--purple);display:flex;justify-content:center;align-items:center;gap:10px;font-family:"Arimo",sans-serif;font-size:10px;color:var(--white)}
.brand{display:flex;justify-content:center;align-items:center;gap:10px;margin-top:10px}
.brand-mark{width:14px;height:14px;border-radius:50%;background:var(--purple)}
.brand-name{font-size:20px;font-weight:400;color:var(--purple-dark);letter-spacing:1px}

.sidebar{position:absolute;left:44px;top:138px;width:252px}
.cat-box{background:var(--lilac);height:460px}
.cat-head{background:var(--lilac-mid);height:70px;display:flex;align-items:center;justify-content:center;text-align:center;font-size:13px;font-weight:600;line-height:19px}
.cat-list{list-style:none;padding-top:5px}
.cat-list li{height:37px;display:flex;align-items:center;padding-left:21px;font-size:11.4px;font-weight:600;color:#333}
.cat-list svg{width:14px;height:14px;margin-right:10px;flex:none}
.ask-box{margin-top:10px;background:var(--lilac);height:95px}
.ask-head{background:var(--purple);color:var(--white);height:42px;padding-left:15px;display:flex;align-items:center;font-size:15px;font-weight:600}
.ask-link{display:flex;align-items:center;gap:10px;padding:14px 0 0 20px;font-size:13px}
.badges{margin-top:23px;display:flex;flex-direction:column;align-items:center;gap:16px}
.badge-rect{width:106px;height:76px;background:#d7e3ec;border-radius:3px}
.badge-wide{width:114px;height:64px;background:#eadfc6;border-radius:3px}
.badge-round{width:96px;height:96px;border-radius:50%;background:#2f5c92}

.main{position:absolute;left:305px;top:138px;width:687px}
.panel{background:var(--lilac);margin-bottom:7px}
.panel-head{background:var(--purple);color:var(--white);height:36px;padding-left:24px;display:flex;align-items:center;font-size:16px;font-weight:600}
.desc{padding:11px 30px 0 24px;font-size:12.8px;line-height:18.5px;height:63px}
.spec{display:grid;grid-template-columns:112px 1fr;row-gap:10px;column-gap:15px;padding:18px 0 17px;font-size:12px;line-height:18px}
.spec dt,.stones dt{text-align:right;white-space:nowrap}
.spec dt::after,.stones dt::after{content:":";margin-left:8px}
.stones{display:grid;grid-template-columns:133px 134px 160px 1fr;row-gap:10px;column-gap:15px;padding:17px 0 0;font-size:12px;line-height:18px}
.natural{padding:24px 0 32px 32px;font-size:12px;line-height:18px;font-weight:700;font-style:italic;color:var(--accent-text)}

.tabs-panel{background:var(--lilac);height:283px;padding:6px 7px}
.tabs{display:flex;align-items:center;font-size:13.4px}
.tab{padding:7px 14.5px;line-height:17px}
.tab.active{background:var(--purple);color:var(--white);font-weight:600;padding:7px 12px;margin-right:6px}
.tab-body{padding:12px 10px 0 8px;font-size:11.1px;line-height:18.5px}
.tab-body .small{font-size:10.4px}
.tab-body h3{font-size:13px;font-weight:700;margin-top:2px;line-height:20px}
.tab-body p{margin-bottom:18px}

.footer-links{position:absolute;left:70px;top:1100px;display:flex;gap:15px;font-family:"Arimo",sans-serif;font-size:10px;color:#555}
.copyright{position:absolute;left:70px;top:1134px;font-family:"Arimo",sans-serif;font-size:8.6px;color:#333}
.copyright u{color:#2a3b8f}
.secure-badge{position:absolute;left:910px;top:1138px;width:62px;height:24px;border-radius:12px;background:#f3e3b0}
.page-code{position:absolute;left:1016px;top:1157px;font-family:"Arimo",sans-serif;font-size:10px;color:#333}
</style>
</head>
<body>
<div class="sheet"></div>
<div class="to-top"><svg width="12" height="9" viewBox="0 0 12 9"><path d="M1 8 6 3 11 8" fill="none" stroke="#222" stroke-width="2.4"/></svg></div>

<header class="masthead">
  <nav class="topnav"><span>About Us</span><span>|</span><span>FAQs</span><span>|</span><span>Why Buy From Us</span><span>|</span><span>Save Seller</span></nav>
  <div class="brand"><span class="brand-mark"></span><span class="brand-name">MIRROW CRAFT NEVADA</span></div>
</header>

<aside class="sidebar">
  <div class="cat-box">
    <div class="cat-head">Please choose a category below<br>to see more subcategories</div>
    <ul class="cat-list">
      <li><svg viewBox="0 0 14 14"><path d="M2 5 7 12 12 5 10 2H4Z" fill="#444"/></svg>Diamond Engagement Rings</li>
      <li><svg viewBox="0 0 14 14"><circle cx="7" cy="8.5" r="4" fill="none" stroke="#444" stroke-width="1.6"/><path d="M5 3h4l-2 2Z" fill="#444"/></svg>Fancy Yellow &amp; Pink Diamond</li>
      <li><svg viewBox="0 0 14 14"><circle cx="7" cy="8.5" r="4" fill="none" stroke="#444" stroke-width="1.6"/><circle cx="7" cy="3" r="1.5" fill="#444"/></svg>Cocktail Fashion Diamond Rings</li>
      <li><svg viewBox="0 0 14 14"><circle cx="7" cy="8" r="3.5" fill="none" stroke="#444" stroke-width="1.6"/><path d="M1 13h12" stroke="#444" stroke-width="1.6"/></svg>Colored Gemstone Diamond Rings</li>
      <li><svg viewBox="0 0 14 14"><ellipse cx="7" cy="8" rx="4" ry="5" fill="none" stroke="#444" stroke-width="1.6"/></svg>Semi Mount Diamond Rings</li>
      <li><svg viewBox="0 0 14 14"><ellipse cx="7" cy="8" rx="6" ry="3.5" fill="none" stroke="#444" stroke-width="1.6"/></svg>Men's Diamond Jewelry</li>
      <li><svg viewBox="0 0 14 14"><path d="M10 2 5 8" stroke="#444" stroke-width="1.4"/><circle cx="5" cy="10" r="2.5" fill="none" stroke="#444" stroke-width="1.4"/></svg>Diamond Pendants</li>
      <li><svg viewBox="0 0 14 14"><circle cx="4" cy="9" r="2.5" fill="none" stroke="#444" stroke-width="1.4"/><circle cx="10" cy="9" r="2.5" fill="none" stroke="#444" stroke-width="1.4"/><path d="M4 2v4M10 2v4" stroke="#444" stroke-width="1.4"/></svg>Diamond Earrings</li>
      <li><svg viewBox="0 0 14 14"><path d="M1 3q6 5 12 0" fill="none" stroke="#444" stroke-width="1.4"/><circle cx="7" cy="10" r="2.5" fill="none" stroke="#444" stroke-width="1.4"/></svg>Diamond Necklaces</li>
      <li><svg viewBox="0 0 14 14"><path d="M10 2A5 5 0 1 0 10 12" fill="none" stroke="#444" stroke-width="1.6"/></svg>Diamond Bracelets &amp; Bangles</li>
    </ul>
  </div>
  <div class="ask-box">
    <div class="ask-head">Questions?</div>
    <div class="ask-link"><svg width="15" height="11" viewBox="0 0 15 11"><rect x="0.8" y="0.8" width="13.4" height="9.4" fill="none" stroke="#333" stroke-width="1.4"/><path d="M1 1l6.5 5L14 1" fill="none" stroke="#333" stroke-width="1.4"/></svg>Ask a question via email</div>
  </div>
  <div class="badges">
    <div class="badge-rect" role="img" aria-label="Accreditation badge"></div>
    <div class="badge-wide" role="img" aria-label="Gem institute badge"></div>
    <div class="badge-round" role="img" aria-label="Gem laboratory seal"></div>
  </div>
</aside>

<main class="main">
  <section class="panel">
    <h2 class="panel-head">Item Description</h2>
    <p class="desc">Exquisite Oval Aquamarine Gemstone Surrounded By A Delicate Halo Of Diamonds Mounted In A Classic 14k Yellow Gold Setting</p>
  </section>
  <section class="panel">
    <h2 class="panel-head">Item Details</h2>
    <dl class="spec">
      <dt>Model Number</dt><dd>MCN-QR72514BTL-300</dd>
      <dt>Metal</dt><dd>14k Yellow Gold</dd>
      <dt>Weight</dt><dd>4.08 grams</dd>
      <dt>L x W x H</dt><dd>12 x 10 x 7.2 MM</dd>
      <dt>Style</dt><dd>Halo</dd>
      <dt>Ring Size</dt><dd>6 (contact us for sizing options)</dd>
    </dl>
  </section>
  <section class="panel">
    <h2 class="panel-head">Diamond Details</h2>
    <dl class="stones">
      <dt>Total Carat Weight</dt><dd>0.19 CT</dd><dt>Other Shape</dt><dd>Round</dd>
      <dt>Diamond Count</dt><dd>22</dd><dt>Other Color/Clarity</dt><dd>G / SI1</dd>
      <dt>Shape</dt><dd>Round</dd><dt>Certificate</dt><dd>GCL (click for more info)</dd>
      <dt>Color/Clarity</dt><dd>G / SI1</dd>
    </dl>
    <p class="natural">All of our diamonds and gemstones are 100% natural!</p>
  </section>
  <section class="tabs-panel">
    <div class="tabs"><span class="tab active">Shipping Details</span><span class="tab">Product Guarantee</span><span class="tab">Return Policy</span><span class="tab">Privacy Policy</span><span class="tab">Why Us</span></div>
    <div class="tab-body">
      <div class="small">Parcelway 2 Day: Free (U.S.A. only)</div>
      <h3>WE SHIP WORLDWIDE</h3>
      <p>International Buyers - Please Note: Import duties, taxes, and charges are not included in the item price or shipping cost. These charges are the buyer's responsibility. Please check with your country's customs office to determine what these additional costs will be prior to bidding or buying.</p>
      <p>All packages are fully insured and require signature confirmation.</p>
      <p>Once your item(s) are ready to leave our facility a shipping tracking number will be sent to you. Business days do not include Saturday, Sunday or holidays. Please be sure to inspect your package upon arrival for tampering or any damage. Rush orders are welcome. Please call for availability.</p>
    </div>
  </section>
</main>

<div class="page-band"><div class="base"></div></div>
<nav class="footer-links"><span>About Quelvo</span><span>Announcements</span><span>Community</span><span>Security Center</span><span>Resolution Center</span><span>Seller Center</span><span>Policies</span><span>Affiliates</span><span>Help &amp; Contact</span><span>Site Map</span></nav>
<p class="copyright">Copyright © 1995-2018 Quelvo Inc. All Rights Reserved. <u>Accessibility</u>, <u>User Agreement</u>, <u>Privacy</u>, <u>Cookies</u> and <u>Ad Options</u></p>
<div class="secure-badge" role="img" aria-label="Secure checkout badge"></div>
<span class="page-code">M1</span>
</body>
</html>
```